New Business Card Design Project

I need a design for business cards, i am an electrical business called "Corvane Electrical and Communications" i need the cards to be double sided with the company logo on the back (attached) the front needs to say my company name, web site, email address, telephone number, and ABN number and electrical license number. I am open to different arrangements of the information but would like the background to be incorporating something electrical or something that looks smart. open to all additional ideas also.

The company colours are orange and grey see logo attached.

Business Name: Corvane Electrical and Communications
Website: corvaneelectricalandcomms.example.com.au
Email: brent@corvaneelectricalandcomms.example.com.au
Telephone(mobile): 0481209736
ABN: 71208349162
Lic No: 418273D

Target Market(s)

Business entities, Project Managers, Accounts, Clients

Industry/Entity Type

Electrician

Contact Information for Business Card

I need a design for business cards, i am an electrical business called "Corvane Electrical and Communications" i need the cards to be double sided with the company logo on the back (attached) the front needs to say my company name

Font styles to use
Serif
Sans Serif

Colors
f37122
5c5c5c

Requirements
Must have
• Must have the Logo on the back open to different ways of it being on the back but had in mind to keep it central but again open to other options
Nice to have
• A real modern cool background that is eye catching yet contemporary
Should not have
• No backgrounds of a light bulb or plug or anything like that

```html
<!DOCTYPE html>
<html lang="en">
<head>
<meta charset="utf-8">
<title>Corvane Electrical and Communications – Business Cards</title>
<link rel="stylesheet" href="https://fonts.googleapis.com/css2?family=Quicksand:wght@500;600;700&family=Exo+2:wght@600&display=swap">
<style>
  :root {
    --orange: #f37122;
    --amber: #f2b21a;
    --grey: #5c5c5c;
    --grey-light: #7a7a7a;
    --charcoal: #4a4a4a;
    --charcoal-dark: #3a3a3a;
    --paper: #ffffff;
    --paper-shade: #f1f1f1;
    --backdrop: #e6e4e0;
  }
  * { box-sizing: border-box; margin: 0; padding: 0; }
  html, body {
    width: 1200px; height: 780px; overflow: hidden;
    background: var(--backdrop);
  }
  .canvas {
    width: 1200px; height: 780px;
    display: flex; align-items: center; justify-content: center; gap: 36px;
  }
  .card {
    position: relative;
    width: 560px; height: 320px;
    border-radius: 4px;
    overflow: hidden;
    box-shadow: 0 6px 18px rgba(0,0,0,.18);
  }

  /* Front */
  .card-front {
    background: linear-gradient(160deg, var(--paper) 40%, var(--paper-shade) 100%);
    font-family: "Quicksand", sans-serif;
    color: var(--grey);
  }
  .front-brand {
    position: absolute; left: 120px; top: 34px; width: 420px;
    font-family: "Exo 2", sans-serif; font-weight: 600;
    color: var(--grey);
    text-transform: uppercase;
    line-height: 1.05;
  }
  .front-brand .brand-word { display: block; font-size: 58px; letter-spacing: 6px; }
  .front-brand .brand-line { display: block; font-size: 15px; letter-spacing: 1.4px; margin-top: 6px; }
  .licence {
    position: absolute; right: 22px; top: 128px;
    font-size: 12px; color: var(--grey-light);
  }
  .licence .label { color: var(--amber); }
  .employee {
    position: absolute; right: 22px; top: 160px; text-align: right;
  }
  .employee .name { font-size: 20px; font-weight: 600; color: var(--grey); }
  .employee .role { font-size: 13px; font-weight: 600; color: var(--amber); }
  .contacts {
    position: absolute; right: 22px; bottom: 22px;
    list-style: none; text-align: right;
    font-size: 11.5px; font-weight: 500; color: var(--grey);
  }
  .contacts li { display: flex; justify-content: flex-end; align-items: center; gap: 6px; height: 17px; }
  .contacts .icon {
    width: 12px; height: 12px; background: var(--amber); border-radius: 2px;
    display: inline-flex; align-items: center; justify-content: center;
  }
  .contacts .abn-label { color: var(--amber); font-weight: 600; }
  .cable-visual {
    position: absolute; left: 0; bottom: 0; width: 200px; height: 150px;
    background:
      linear-gradient(90deg, rgba(214,40,40,.85) 0 22%, rgba(196,140,80,.9) 22% 38%, rgba(40,70,180,.85) 38% 55%, rgba(230,200,40,.85) 55% 72%, rgba(70,70,70,.85) 72% 100%);
    -webkit-mask: linear-gradient(0deg, #000 70%, transparent);
            mask: linear-gradient(0deg, #000 70%, transparent);
  }

  /* Back */
  .card-back {
    background: radial-gradient(ellipse at 40% 40%, var(--charcoal) 0%, var(--charcoal-dark) 100%);
    display: flex; align-items: center; justify-content: center;
  }
  .back-brand {
    font-family: "Exo 2", sans-serif; font-weight: 600;
    color: #ffffff; text-transform: uppercase; text-align: center;
    line-height: 1.1;
  }
  .back-brand .brand-word { display: block; font-size: 64px; letter-spacing: 8px; }
  .back-brand .brand-line { display: block; font-size: 14px; letter-spacing: 1.6px; margin-top: 8px; }
</style>
</head>
<body>
<main class="canvas">
  <section class="card card-front" aria-label="Business card front">
    <h1 class="front-brand">
      <span class="brand-word">Corvane</span>
      <span class="brand-line">Electrical &amp; Communications</span>
    </h1>
    <p class="licence"><span class="label">Lic No:</span> 418273D</p>
    <div class="employee">
      <p class="name">Employee Name</p>
      <p class="role">Principal</p>
    </div>
    <ul class="contacts">
      <li>0481209736
        <span class="icon"><svg width="8" height="8" viewBox="0 0 8 8"><rect x="2" y="0.5" width="4" height="7" rx="0.8" fill="none" stroke="#fff" stroke-width="1"/></svg></span>
      </li>
      <li>brent@corvaneelectricalandcomms.example.com.au
        <span class="icon"><svg width="8" height="8" viewBox="0 0 8 8"><rect x="0.5" y="1.5" width="7" height="5" fill="none" stroke="#fff" stroke-width="1"/><path d="M0.5 1.5 L4 4.5 L7.5 1.5" fill="none" stroke="#fff" stroke-width="1"/></svg></span>
      </li>
      <li>corvaneelectricalandcomms.example.com.au
        <span class="icon"><svg width="8" height="8" viewBox="0 0 8 8"><circle cx="4" cy="4" r="3.3" fill="none" stroke="#fff" stroke-width="1"/><path d="M0.7 4 H7.3 M4 0.7 V7.3" stroke="#fff" stroke-width="0.8"/></svg></span>
      </li>
      <li><span><span class="abn-label">ABN:</span> 71208349162</span></li>
    </ul>
    <div class="cable-visual" role="img" aria-label="Photograph of bundled copper electrical cables in red, blue, yellow and grey sheathing"></div>
  </section>

  <section class="card card-back" aria-label="Business card back">
    <h2 class="back-brand">
      <span class="brand-word">Corvane</span>
      <span class="brand-line">Electrical &amp; Communications</span>
    </h2>
  </section>
</main>
</body>
</html>
```